QuarryDesk Company Powerpoint Template

I would like to create a branded PowerPoint temple that my company can use for all presentations. our website is www.quarrydesk.example. The company is a software provider for the auto recycling industry (junk yards). Our customers use our software to pull, process, and deliver orders to auto body shops and mechanic shops.
Pages that would be helpful:
Title Page
Content slide
Content slide with image
Workflow/flowchart slide
Image only slide
Final slide

Target Market(s)

Automotive Recycling

Industry/Entity Type

Automotive recycling software

Font styles to use
Sans Serif

Colors
0054AA
0677BA
7BADD7
CADEEF
E8F1F8
FFF300
FFF600
FEFA6F
FFFEC7
FFFEE8

Requirements
Must have
• similarities in other branded items like our website. Title Page, Content slide, Content slide with image, Workflow/flowchart slide, Image only slide, Final slide
Nice to have
• Simple clean design would be preferential

```html
<!DOCTYPE html>
<html lang="en">
<head>
<meta charset="utf-8">
<title>QuarryDesk Presentation Template</title>
<link rel="stylesheet" href="https://fonts.googleapis.com/css2?family=Ubuntu:wght@300;400;500;700&display=swap">
<style>
:root{
  --blue:#0054AA;
  --mid:#0677BA;
  --light:#7BADD7;
  --pale:#CADEEF;
  --mist:#E8F1F8;
  --yellow:#FFF300;
  --ink:#444;
  --grey:#777;
  --board:#c9c5c5;
  --stage:#dfe3ea;
}
*{margin:0;padding:0;box-sizing:border-box}
html,body{width:1200px;height:2772px;overflow:hidden}
body{font-family:"Ubuntu",sans-serif;background:var(--board);position:relative;color:var(--ink)}
.stage{position:absolute;left:0;top:0;width:1200px;height:720px;background:linear-gradient(180deg,#e9ecf1,#d3d8df)}
.stage-brand{position:absolute;right:30px;top:62px;font-size:22px;font-weight:700;color:var(--blue)}
.slide{position:absolute;width:562px;height:316px;background:#fff;overflow:hidden}
.hero{left:150px;top:100px;transform:scale(1.6);transform-origin:0 0;box-shadow:0 20px 40px rgba(0,0,0,.18)}
.c1{left:28px}.c2{left:609px}
.r1{top:750px}.r2{top:1085px}.r3{top:1420px}.r4{top:1755px}.r5{top:2090px}.r6{top:2425px}
.abs{position:absolute}
.photo-warehouse{background:linear-gradient(135deg,#b9a27f 0%,#8d8a86 40%,#c7b79a 70%,#7d7f86 100%)}
.photo-engine{background:linear-gradient(120deg,#a8a7a4 0%,#6e6f73 45%,#d6d2cb 75%,#9b9994 100%)}
.brand{font-weight:700;color:var(--blue);font-size:26px;letter-spacing:-.3px}
.brand.light{color:#fff}
.title{font-weight:700;font-size:24px;line-height:1.1}
.rule{position:absolute;width:42px;height:3px;background:var(--yellow)}
.pill{position:absolute;height:15px;font-size:6.5px;letter-spacing:.6px;color:#fff;display:flex;align-items:center;justify-content:center}
.heading{position:absolute;left:33px;top:28px;font-size:21px;color:var(--blue);font-weight:400}
.sub{position:absolute;left:33px;top:73px;font-size:6.5px;color:var(--grey)}
.body{position:absolute;font-size:6.2px;line-height:1.35;color:var(--grey)}
.body p{margin-bottom:6px}
.foot-brand{position:absolute;left:14px;bottom:10px;font-size:11px;font-weight:700;color:var(--blue)}
.foot-meta{position:absolute;right:14px;bottom:12px;font-size:4.8px;color:#333;letter-spacing:.1px}
.foot-meta b{color:var(--blue);font-weight:400;margin-left:6px;padding-left:6px;border-left:1px solid var(--light)}
.toc{position:absolute;left:292px;top:100px;width:210px;list-style:none}
.toc li{display:flex;gap:16px;font-size:15px;color:#555;padding:6px 0;border-bottom:1px solid #e4e4e4}
.toc li span{color:var(--pale);width:18px}
.team{position:absolute;top:108px;width:90px;text-align:center}
.avatar{width:86px;height:86px;border-radius:50%;border:3px solid #fff;margin:0 auto;background:linear-gradient(160deg,#c3ccd8,#5b7fae)}
.team .name{font-size:10px;color:var(--blue);margin-top:8px}
.team .info{font-size:5px;color:var(--grey);margin-top:5px;line-height:1.9}
.step{position:absolute;width:90px;text-align:center}
.step h4{font-size:8px;font-weight:400;color:var(--grey)}
.step p{font-size:5px;color:var(--grey);line-height:1.25;margin-top:3px}
.contact{position:absolute;left:55px;top:145px;color:#fff}
.contact h3{font-size:10px;font-weight:700;margin-bottom:8px}
.contact p{font-size:6.5px;margin-bottom:8px;display:flex;align-items:center;gap:7px}
</style>
</head>
<body>

<section class="stage">
  <div class="stage-brand">QuarryDesk</div>
</section>

<!-- Title slide (featured) -->
<article class="slide hero">
  <div class="abs photo-warehouse" role="img" aria-label="Warehouse aisle with tall shelves of boxed auto parts" style="left:290px;top:0;width:272px;height:290px;opacity:.55"></div>
  <div class="abs brand" style="left:36px;top:38px">QuarryDesk</div>
  <div class="abs" style="left:0;top:102px;width:562px;height:188px;background:linear-gradient(90deg,var(--blue) 0%,var(--blue) 45%,rgba(0,84,170,.75) 100%)"></div>
  <div class="abs title" style="left:33px;top:124px;color:#fff">Transforming<br>Automotive Recycling</div>
  <div class="rule" style="left:33px;top:192px"></div>
  <div class="abs" style="left:33px;top:203px;font-size:6.5px;color:#fff;width:290px;line-height:1.3">QuarryDesk offers a wide range of consulting services with the necessary tools and expertise to help grow your business.</div>
  <div class="pill" style="left:33px;top:248px;width:115px;background:#0a3f8e">www.quarrydesk.example</div>
  <div class="abs" style="left:0;top:297px;width:562px;text-align:center;font-size:5px;color:#555">© 2020 by QuarryDesk.</div>
</article>

<!-- Row 1 -->
<article class="slide c1 r1">
  <div class="abs photo-warehouse" role="img" aria-label="Warehouse aisle with tall shelves of boxed auto parts" style="left:290px;top:0;width:272px;height:290px;opacity:.55"></div>
  <div class="abs brand" style="left:36px;top:38px">QuarryDesk</div>
  <div class="abs" style="left:0;top:102px;width:562px;height:188px;background:linear-gradient(90deg,var(--blue) 0%,var(--blue) 45%,rgba(0,84,170,.75) 100%)"></div>
  <div class="abs title" style="left:33px;top:124px;color:#fff">Transforming<br>Automotive Recycling</div>
  <div class="rule" style="left:33px;top:192px"></div>
  <div class="abs" style="left:33px;top:203px;font-size:6.5px;color:#fff;width:290px;line-height:1.3">QuarryDesk offers a wide range of consulting services with the necessary tools and expertise to help grow your business.</div>
  <div class="pill" style="left:33px;top:248px;width:115px;background:#0a3f8e">www.quarrydesk.example</div>
  <div class="abs" style="left:0;top:297px;width:562px;text-align:center;font-size:5px;color:#555">© 2020 by QuarryDesk.</div>
</article>

<article class="slide c2 r1">
  <div class="abs photo-warehouse" role="img" aria-label="Worker on an order picker lift in a parts warehouse" style="left:180px;top:0;width:382px;height:316px"></div>
  <svg class="abs" style="left:0;top:0" width="562" height="316" viewBox="0 0 562 316">
    <polygon points="0,0 185,0 365,175 365,190 205,316 0,316" fill="#fff"/>
    <polygon points="185,0 385,0 285,100" fill="#0054AA" opacity=".9"/>
    <polygon points="200,316 310,245 360,316" fill="#0054AA"/>
  </svg>
  <div class="abs brand" style="left:33px;top:52px">QuarryDesk</div>
  <div class="abs title" style="left:33px;top:124px;color:var(--blue)">Presentation<br>Title Goes Here!</div>
  <div class="rule" style="left:33px;top:188px"></div>
  <div class="abs" style="left:33px;top:203px;font-size:7px;color:var(--grey)">Transforming Automotive Recycling</div>
  <div class="pill" style="left:33px;top:248px;width:110px;background:var(--blue)">December 4, 2022</div>
  <div class="abs" style="left:255px;top:290px;font-size:5px;color:#fff;text-align:center;line-height:1.5">www.quarrydesk.example<br>©2020 by QuarryDesk.</div>
</article>

<!-- Row 2 -->
<article class="slide c1 r2">
  <div class="abs photo-engine" role="img" aria-label="Technician checking a tablet beside an engine on a hoist" style="left:180px;top:0;width:382px;height:316px"></div>
  <svg class="abs" style="left:0;top:0" width="562" height="316" viewBox="0 0 562 316">
    <polygon points="0,0 385,0 285,100 365,180 205,316 0,316" fill="#0054AA"/>
    <polygon points="185,0 385,0 285,100" fill="#0677BA" opacity=".6"/>
    <polygon points="200,316 290,245 355,316" fill="#7BADD7"/>
  </svg>
  <div class="abs brand light" style="left:33px;top:52px">QuarryDesk</div>
  <div class="abs title" style="left:33px;top:124px;color:#fff">Presentation<br>Title Goes Here!</div>
  <div class="rule" style="left:33px;top:188px"></div>
  <div class="abs" style="left:33px;top:203px;font-size:7px;color:#fff">Transforming Automotive Recycling</div>
  <div class="pill" style="left:33px;top:248px;width:110px;background:var(--light)">December 4, 2022</div>
  <div class="abs" style="left:237px;top:290px;font-size:5px;color:var(--blue);text-align:center;line-height:1.5">www.quarrydesk.example<br>©2020 by QuarryDesk.</div>
</article>

<article class="slide c2 r2">
  <div class="abs brand" style="left:40px;top:130px;font-size:34px">QuarryDesk</div>
  <div class="heading" style="left:300px;top:38px">Content</div>
  <div class="rule" style="left:300px;top:70px"></div>
  <ol class="toc">
    <li><span>01</span>Title Goes Here</li>
    <li><span>02</span>Title Goes Here</li>
    <li><span>03</span>Title Goes Here</li>
    <li><span>04</span>Title Goes Here</li>
    <li><span>05</span>Title Goes Here</li>
  </ol>
  <div class="foot-brand">QuarryDesk</div>
  <div class="foot-meta">WWW.QUARRYDESK.EXAMPLE | ©2020 BY QUARRYDESK.<b>4</b></div>
</article>

<!-- Row 3 -->
<article class="slide c1 r3">
  <h2 class="heading">Heading Goes Here</h2>
  <div class="rule" style="left:33px;top:60px"></div>
  <div class="sub">Sub-Heading Goes Here</div>
  <div class="body" style="left:33px;top:102px;width:496px">
    <p>Lorem ipsum dolor sit amet, consectetur adipiscing elit. Vivamus eu dui ex. Curabitur dapibus dignissim dui, in molestie metus feugiat sed. Praesent aliquet lorem ex, eu dapibus odio varius at. Duis eget tellus porta, consequat lacus vitae, venenatis dolor. Nulla facilisi. In et sollicitudin lacus. Donec risus orci, gravida sit amet risus vehicula, aliquet pretium sapien. Nullam sit amet magna non ex bibendum mollis. Nunc vel neque eu augue dignissim congue ut vitae magna. Phasellus eget commodo arcu. Nunc vitae semper dui. Integer venenatis, tellus sit amet interdum pretium, erat neque rhoncus turpis, a aliquam augue ligula eget erat. Nunc placerat, arcu nec mattis fermentum, nisi mauris convallis nunc, ut luctus nunc nisl id ex. Nam semper tristique mauris, et vestibulum leo fringilla vel. Nulla id augue eleifend, egestas ligula et, consequat massa. Pellentesque habitant morbi tristique senectus et netus et malesuada fames ac turpis egestas.</p>
    <p>Lorem ipsum dolor sit amet, consectetur adipiscing elit. Vivamus eu dui ex. Curabitur dapibus dignissim dui, in molestie metus feugiat sed. Praesent aliquet lorem ex, eu dapibus odio varius at. Duis eget tellus porta, consequat lacus vitae, venenatis dolor. Nulla facilisi. In et sollicitudin lacus.</p>
    <p>Donec risus orci, gravida sit amet risus vehicula, aliquet pretium sapien. Nullam sit amet magna non ex bibendum mollis. Nunc vel neque eu augue dignissim congue ut vitae magna. Phasellus eget commodo arcu. Nunc vitae semper dui. Integer venenatis, tellus sit amet interdum pretium, erat neque rhoncus turpis, a aliquam augue ligula eget erat. Nunc placerat, arcu nec mattis fermentum, nisi mauris convallis nunc, ut luctus nunc nisl id ex. Nam semper tristique mauris, et vestibulum leo fringilla vel. Nulla id augue eleifend, egestas ligula et, consequat massa. Pellentesque habitant morbi tristique senectus et netus et malesuada fames ac turpis egestas.</p>
  </div>
  <div class="foot-brand">QuarryDesk</div>
  <div class="foot-meta">WWW.QUARRYDESK.EXAMPLE | ©2020 BY QUARRYDESK.<b>5</b></div>
</article>

<article class="slide c2 r3">
  <h2 class="heading">Column Slide</h2>
  <div class="rule" style="left:33px;top:60px"></div>
  <div class="sub">Sub-Heading Goes Here</div>
  <div class="body" style="left:33px;top:102px;width:236px">
    <p>Lorem ipsum dolor sit amet, consectetur adipiscing elit. Vivamus eu dui ex. Curabitur dapibus dignissim dui, in molestie metus feugiat sed. Praesent aliquet lorem ex, eu dapibus odio varius at. Duis eget tellus porta, consequat lacus vitae, venenatis dolor. Nulla facilisi. In et sollicitudin lacus.</p>
    <p>Nunc placerat, arcu nec mattis fermentum, nisi mauris convallis nunc, ut luctus nunc nisl id ex. Nam semper tristique mauris, et vestibulum leo fringilla vel. Nulla id augue eleifend, egestas ligula et, consequat massa. Pellentesque habitant morbi tristique senectus et netus et malesuada fames ac turpis egestas.</p>
    <p>Donec risus orci, gravida sit amet risus vehicula, aliquet pretium sapien. Nullam sit amet magna non ex bibendum mollis. Nunc vel neque eu augue dignissim congue ut vitae magna. Phasellus eget commodo arcu. Nunc vitae semper dui. Integer venenatis, tellus sit amet interdum pretium, erat neque rhoncus turpis, a aliquam augue ligula eget erat.</p>
  </div>
  <div class="body" style="left:295px;top:102px;width:236px">
    <p>Lorem ipsum dolor sit amet, consectetur adipiscing elit. Vivamus eu dui ex. Curabitur dapibus dignissim dui, in molestie metus feugiat sed. Praesent aliquet lorem ex, eu dapibus odio varius at. Duis eget tellus porta, consequat lacus vitae, venenatis dolor. Nulla facilisi. In et sollicitudin lacus.</p>
    <p>Nunc placerat, arcu nec mattis fermentum, nisi mauris convallis nunc, ut luctus nunc nisl id ex. Nam semper tristique mauris, et vestibulum leo fringilla vel. Nulla id augue eleifend, egestas ligula et, consequat massa. Pellentesque habitant morbi tristique senectus et netus et malesuada fames ac turpis egestas.</p>
    <p>Donec risus orci, gravida sit amet risus vehicula, aliquet pretium sapien. Nullam sit amet magna non ex bibendum mollis. Nunc vel neque eu augue dignissim congue ut vitae magna. Phasellus eget commodo arcu. Nunc vitae semper dui. Integer venenatis, tellus sit amet interdum pretium, erat neque rhoncus turpis, a aliquam augue ligula eget erat.</p>
  </div>
  <div class="foot-brand">QuarryDesk</div>
  <div class="foot-meta">WWW.QUARRYDESK.EXAMPLE | ©2020 BY QUARRYDESK.<b>6</b></div>
</article>

<!-- Row 4 -->
<article class="slide c1 r4">
  <h2 class="heading">Heading Goes Here</h2>
  <div class="rule" style="left:33px;top:60px"></div>
  <div class="sub">Sub-Heading Goes Here</div>
  <div class="body" style="left:33px;top:102px;width:250px">
    <p>Lorem ipsum dolor sit amet, consectetur adipiscing elit. Vivamus eu dui ex. Curabitur dapibus dignissim dui, in molestie metus feugiat sed. Praesent aliquet lorem ex, eu dapibus odio varius at. Duis eget tellus porta, consequat lacus vitae, venenatis dolor.</p>
    <p>Nulla facilisi. In et sollicitudin lacus. Donec risus orci, gravida sit amet risus vehicula, aliquet pretium sapien. Nullam sit amet magna non ex bibendum mollis.</p>
    <p>Nunc vel neque eu augue dignissim congue ut vitae magna. Phasellus eget commodo arcu. Nunc vitae semper dui. Integer venenatis, tellus sit amet interdum pretium, erat neque rhoncus turpis, a aliquam augue ligula eget erat.</p>
    <p>Nunc placerat, arcu nec mattis fermentum, nisi mauris convallis nunc, ut luctus nunc nisl id ex. Nam semper tristique mauris, et vestibulum leo fringilla vel. Nulla id augue eleifend, egestas ligula et, consequat massa. Pellentesque habitant morbi tristique senectus et netus et malesuada fames ac turpis egestas.</p>
  </div>
  <div class="abs photo-warehouse" role="img" aria-label="Worker on an order picker lift in a parts warehouse" style="left:305px;top:28px;width:228px;height:234px"></div>
  <div class="foot-brand">QuarryDesk</div>
  <div class="foot-meta">WWW.QUARRYDESK.EXAMPLE | ©2020 BY QUARRYDESK.<b>7</b></div>
</article>

<article class="slide c2 r4">
  <div class="abs" style="left:0;top:0;width:562px;height:148px;background:var(--blue)"></div>
  <h2 class="heading" style="color:#fff">Meet <b style="font-weight:700">Our Team</b></h2>
  <div class="rule" style="left:33px;top:60px"></div>
  <div class="team" style="left:34px"><div class="avatar" role="img" aria-label="Team member portrait"></div><div class="name">Reed Halvorsen</div><div class="info">President</div></div>
  <div class="team" style="left:135px"><div class="avatar" role="img" aria-label="Team member portrait"></div><div class="name">Mara Lindqvist</div><div class="info">mara@quarrydesk.example<br>ext. 125</div></div>
  <div class="team" style="left:236px"><div class="avatar" role="img" aria-label="Team member portrait"></div><div class="name">Theo Barrett</div><div class="info">theo@quarrydesk.example<br>ext. 126</div></div>
  <div class="team" style="left:337px"><div class="avatar" role="img" aria-label="Team member portrait"></div><div class="name">Iris Calloway</div><div class="info">iris@quarrydesk.example<br>ext. 124</div></div>
  <div class="team" style="left:438px"><div class="avatar" role="img" aria-label="Team member portrait"></div><div class="name">Owen Pratt</div><div class="info">owen@quarrydesk.example<br>ext. 128</div></div>
  <div class="foot-brand">QuarryDesk</div>
  <div class="foot-meta">WWW.QUARRYDESK.EXAMPLE | ©2020 BY QUARRYDESK.<b>8</b></div>
</article>

<!-- Row 5 -->
<article class="slide c1 r5">
  <h2 class="heading">Workflow / Flowchart Slide</h2>
  <div class="rule" style="left:33px;top:60px"></div>
  <svg class="abs" style="left:0;top:0" width="562" height="316" viewBox="0 0 562 316">
    <g fill="none" stroke-width="7">
      <path d="M32,172 A50,50 0 0 1 132,172" stroke="#0054AA"/>
      <path d="M132,172 A50,50 0 0 0 232,172" stroke="#7BADD7"/>
      <path d="M232,172 A50,50 0 0 1 332,172" stroke="#0054AA"/>
      <path d="M332,172 A50,50 0 0 0 432,172" stroke="#7BADD7"/>
      <path d="M432,172 A50,50 0 0 1 532,172" stroke="#0054AA"/>
    </g>
    <g fill="#0054AA"><polygon points="126,176 138,176 132,186"/><polygon points="326,176 338,176 332,186"/></g>
    <g fill="#7BADD7"><polygon points="226,168 238,168 232,158"/><polygon points="426,168 438,168 432,158"/></g>
    <circle cx="82" cy="172" r="33" fill="#0054AA"/>
    <circle cx="182" cy="172" r="33" fill="#7BADD7"/>
    <circle cx="282" cy="172" r="33" fill="#0054AA"/>
    <circle cx="382" cy="172" r="33" fill="#7BADD7"/>
    <circle cx="482" cy="172" r="33" fill="#0054AA"/>
    <g fill="#fff" stroke="#fff">
      <circle cx="82" cy="167" r="9" stroke="none"/><rect x="78" y="176" width="8" height="7" stroke="none"/>
      <circle cx="175" cy="165" r="5" stroke="none"/><circle cx="189" cy="165" r="5" stroke="none"/>
      <path d="M166,182 a9,8 0 0 1 18,0 z M180,182 a9,8 0 0 1 18,0 z" stroke="none"/>
      <circle cx="279" cy="169" r="9" fill="none" stroke-width="4"/><line x1="286" y1="176" x2="294" y2="184" stroke-width="5"/>
      <circle cx="382" cy="172" r="11" fill="none" stroke-width="6" stroke-dasharray="4 2.5"/><circle cx="382" cy="172" r="5" fill="none" stroke-width="3"/>
      <rect x="470" y="175" width="6" height="10" stroke="none"/><rect x="479" y="170" width="6" height="15" stroke="none"/><rect x="488" y="164" width="6" height="21" stroke="none"/>
      <polyline points="469,170 480,162 486,165 495,157" fill="none" stroke-width="2"/>
    </g>
  </svg>
  <div class="step" style="left:137px;top:86px"><h4>Heading</h4><p>Nunc vel neque eu augue dignissim congue ut vitae magna. Phasellus eget commodo arcu.</p></div>
  <div class="step" style="left:337px;top:86px"><h4>Heading</h4><p>Nunc vel neque eu augue dignissim congue ut vitae magna. Phasellus eget commodo arcu.</p></div>
  <div class="step" style="left:37px;top:222px"><h4>Heading</h4><p>Nunc vel neque eu augue dignissim congue ut vitae magna. Phasellus eget commodo arcu.</p></div>
  <div class="step" style="left:237px;top:222px"><h4>Heading</h4><p>Nunc vel neque eu augue dignissim congue ut vitae magna. Phasellus eget commodo arcu.</p></div>
  <div class="step" style="left:437px;top:222px"><h4>Heading</h4><p>Nunc vel neque eu augue dignissim congue ut vitae magna. Phasellus eget commodo arcu.</p></div>
  <div class="foot-brand">QuarryDesk</div>
  <div class="foot-meta">WWW.QUARRYDESK.EXAMPLE | ©2020 BY QUARRYDESK.<b>9</b></div>
</article>

<article class="slide c2 r5">
  <div class="abs photo-engine" role="img" aria-label="Technician checking a tablet beside an engine on a hoist" style="left:29px;top:28px;width:504px;height:236px"></div>
  <div class="foot-brand">QuarryDesk</div>
  <div class="foot-meta">WWW.QUARRYDESK.EXAMPLE | ©2020 BY QUARRYDESK.<b>10</b></div>
</article>

<!-- Row 6 -->
<article class="slide c1 r6">
  <div class="abs photo-warehouse" role="img" aria-label="Worker on an order picker lift in a parts warehouse" style="left:0;top:0;width:562px;height:282px"></div>
  <div class="foot-brand">QuarryDesk</div>
  <div class="foot-meta">WWW.QUARRYDESK.EXAMPLE | ©2020 BY QUARRYDESK.<b>11</b></div>
</article>

<article class="slide c2 r6" style="background:var(--blue)">
  <div class="abs photo-warehouse" role="img" aria-label="Faint warehouse aisle behind the blue background" style="left:0;top:0;width:562px;height:316px;opacity:.18"></div>
  <div class="abs brand light" style="left:55px;top:92px">QuarryDesk</div>
  <div class="contact">
    <h3>Contact Us</h3>
    <p>48 Granite Way, Ridgefield, OH 00000</p>
    <p><svg width="9" height="9" viewBox="0 0 24 24"><path fill="#fff" d="M6.6 10.8a15 15 0 0 0 6.6 6.6l2.2-2.2a1 1 0 0 1 1-.25 11 11 0 0 0 3.6.6 1 1 0 0 1 1 1V20a1 1 0 0 1-1 1A17 17 0 0 1 3 4a1 1 0 0 1 1-1h3.5a1 1 0 0 1 1 1 11 11 0 0 0 .6 3.6 1 1 0 0 1-.25 1z"/></svg>555-014-0100</p>
    <p><svg width="9" height="9" viewBox="0 0 24 24"><circle cx="12" cy="12" r="4" fill="none" stroke="#fff" stroke-width="2.5"/><path d="M16 12v2a3 3 0 0 0 6 0v-2a10 10 0 1 0-4 8" fill="none" stroke="#fff" stroke-width="2.5"/></svg>support@quarrydesk.example</p>
    <p><svg width="9" height="9" viewBox="0 0 24 24"><g fill="none" stroke="#fff" stroke-width="2"><circle cx="12" cy="12" r="10"/><ellipse cx="12" cy="12" rx="4" ry="10"/><line x1="2" y1="12" x2="22" y2="12"/></g></svg>www.quarrydesk.example</p>
  </div>
  <div class="abs" style="left:0;top:296px;width:562px;text-align:center;font-size:4.5px;color:#fff">©2020 by QuarryDesk.</div>
</article>

</body>
</html>
```